Website Redesign for Non-Profit Ministry & Church

NOTE: Please do not contact me privately — all private inquiries will be ignored.

Individuals seeking spiritual healing, community connection, ministry support and journal-based encounters.

Description of What’s Needed

We need a clean, fresh, inviting website that encourages engagement and connection. The site should feel warm and accessible, draw people in, and clearly present who we are, what we offer, and how visitors can participate. The layout should be straightforward, with well-structured pages (no overlapping objects, minimal layering complexity) and easy to navigate. Use only Google Fonts. All stock photos must be sourced from royalty-free sites and include proper attribution. We will not include a search feature.

Pages to Create
1. Home Page – impactful hero area, clear call-to-action, visual story of ministry, giving/gathering invitation.
2. About Us – vision, mission, leadership, testimonies, history.
3. Meetings & Events – upcoming gatherings, schedule, how to attend, sign-up or interest form.
4. Encounter: “Lanterns by the River” (book) – dedicated page for the book, overview, purchase link or details, journal prompts, imagery.
5. Healing Rooms / Ministry – explain ministry offerings, invite participation, testimonials or case-studies.
6. Live Stream & Links Page – page listing links for YouTube live stream, other platforms, archive links; simple layout.

Colour & Branding

Use colours that blend with our existing logo (attached). The palette should feel contemporary, welcoming, and aligned with ministry themes of restoration, healing and love. Ensure text, button and link colours maintain good contrast for accessibility.

Existing Content & Reference

Please gather available content from our current website in the attachment here for text, images and structure for reuse.

Imagery Guidelines

– Use original photos from our Facebook page or Google Location listing for building or people images when available.
– If generic images are used, ensure they depict appropriate ministry-related buildings or people (community, warm gathering) — avoid generic unrelated stock imagery.
– All photos must be royalty-free or have proper licensing and attribution.
– No overlapping objects or visual clutter; clean layouts with defined sections.

Additional Notes

– Integration: We currently utilise MailChimp for email communication; the design should include a connection/invite to subscribe (via MailChimp) but no blog page is required at this time.
– Payment/Giving: We accept PayPal and already have a giving portal; include clear donation/give buttons or calls-to-action linking to existing giving systems.
– No search function to be included.
– Layouts should avoid complex layering or overlapping elements—designers should work with distinct content blocks, clear visual hierarchy, and straightforward mobile-friendly structure.

Target Market(s)

Industry/Entity Type

Church/Religious institution

Number of Pages Required

5+ page

Requirements
Should not have
• search bar

```html
<!DOCTYPE html>
<html lang="en">
<head>
<meta charset="utf-8">
<title>Mended Held Whole</title>
<link href="https://fonts.googleapis.com/css2?family=Montserrat:wght@400;500;600;700&display=swap" rel="stylesheet">
<style>
:root{
  --teal:#009485;
  --teal-dark:#007d70;
  --ink:#111;
  --text:#3a3a3a;
  --mist:#edf4f5;
  --white:#fff;
}
*{box-sizing:border-box;margin:0;padding:0}
html,body{width:1200px;height:2446px;overflow:hidden}
body{font-family:"Montserrat",sans-serif;color:var(--text);background:var(--white);position:relative}
.abs{position:absolute}
.brand{display:flex;align-items:center;gap:8px;color:var(--teal);font-weight:700}
.brand-dot{width:14px;height:14px;border-radius:50%;background:var(--teal)}
/* header */
.site-header{position:absolute;left:0;top:0;width:1200px;height:95px;background:var(--white)}
.site-header .brand{position:absolute;left:76px;top:34px;font-size:20px}
.main-nav{position:absolute;right:75px;top:37px;display:flex;gap:30px;font-size:14.5px;color:#333}
.main-nav .active{font-weight:700;color:var(--ink)}
/* hero */
.hero{position:absolute;left:0;top:95px;width:1200px;height:532px;background:linear-gradient(120deg,#3c3a3c 0%,#6b6a72 40%,#b9b6b3 62%,#5d5650 100%)}
.hero-card{position:absolute;left:76px;top:109px;width:489px;height:314px;border-radius:22px;background:rgba(0,148,133,.72);padding:38px 26px}
.hero-card h1{color:#fff;font-size:48px;line-height:53px;font-weight:600}
.hero-card p{color:#fff;font-size:17px;line-height:26px;margin-top:18px}
.btn{display:inline-block;background:var(--teal);color:#fff;border-radius:10px;font-size:15px;font-weight:500}
.hero-card .btn{margin-top:20px;padding:9px 26px;background:#0aa596}
/* about */
.about-frame{left:117px;top:742px;width:425px;height:410px;border:2px solid var(--teal)}
.about-corner{left:112px;top:1042px;width:8px;height:117px;background:var(--teal)}
.about-corner2{left:112px;top:1151px;width:113px;height:8px;background:var(--teal)}
.about-photo{left:147px;top:712px;width:425px;height:411px;border:2px solid var(--teal);border-radius:24px;background:linear-gradient(135deg,#8d8f96,#c9c0b3 50%,#3f3d5c)}
.icon{width:42px;height:38px;border-radius:50%;border:3px solid var(--teal)}
.section-title{color:var(--ink);font-size:40px;font-weight:600;line-height:46px}
.about-text{left:646px;top:712px;width:446px}
.about-text .section-title{margin-top:8px}
.body-copy{font-size:15.5px;line-height:25.6px;margin-top:6px}
.about-text .first{margin-top:24px}
.accordion{left:650px;width:447px;height:37px;border:1.5px solid #9aa;border-radius:9px;padding:0 14px;display:flex;align-items:center;justify-content:space-between;font-size:15px;color:#222;font-weight:500}
/* community */
.community{left:0;top:1261px;width:1200px;height:547px;background:var(--mist)}
.community-text{left:113px;top:1363px;width:480px}
.community-text .section-title{margin-top:8px}
.community-text .lead{font-size:15.5px;line-height:25.6px;color:#111;margin-top:20px}
.community-text .btn{margin-top:16px;padding:9px 19px}
.tile{border:2px solid var(--teal);border-radius:8px}
/* newsletter */
.newsletter{left:0;top:1808px;width:1200px;height:357px;background:var(--teal);text-align:center;color:#fff}
.newsletter .icon{border-color:#fff;margin:87px auto 0}
.newsletter h2{font-size:40px;font-weight:600;line-height:46px;margin-top:10px}
.newsletter p{font-size:15.5px;margin-top:8px}
.field{top:2040px;height:37px;border:1.5px solid #fff;border-radius:10px;color:#fff;font-size:15px;padding:9px 18px}
.subscribe{top:2040px;left:836px;width:191px;height:37px;border-radius:10px;background:#fff;color:var(--teal);font-size:15px;text-align:center;line-height:37px}
/* footer */
.site-footer .brand{position:absolute;left:0;width:1200px;justify-content:center;top:2252px;font-size:30px}
.footer-nav{left:0;width:1200px;top:2348px;display:flex;justify-content:center;gap:30px;font-size:14.5px;color:#333}
.footer-rule{left:111px;top:2381px;width:977px;height:1px;background:#bbb}
.copyright{left:111px;top:2400px;font-size:12px;color:#333}
.social{top:2397px;width:21px;height:21px;border-radius:3px;background:var(--ink)}
</style>
</head>
<body>
<header class="site-header">
  <div class="brand"><span class="brand-dot"></span>Mended Held Whole</div>
  <nav class="main-nav">
    <span class="active">Home</span><span>About Us</span><span>Meetings &amp; Events</span><span>Lanterns by the River</span><span>Healing Rooms</span><span>Live Stream</span>
  </nav>
</header>

<section class="hero" role="img" aria-label="Congregation worshipping with raised hands in a church sanctuary with a cross on the wall">
  <div class="hero-card">
    <h1>Mended, Held, Whole</h1>
    <p>A community where you can encounter God’s love and find restoration</p>
    <span class="btn">Join Us This Week</span>
  </div>
</section>

<div class="abs about-frame"></div>
<div class="abs about-corner"></div>
<div class="abs about-corner2"></div>
<div class="abs about-photo" role="img" aria-label="Portrait of the ministry founders, a married couple standing before a stained glass window"></div>
<div class="abs about-text">
  <div class="icon"></div>
  <h2 class="section-title">About Us</h2>
  <p class="body-copy first">Daniel and Ruth Ann have been married for 42 years and have two adult children. They both grew up in southern Ohio. Their desire is to share the love of Christ with others. They have numerous stories to share about the many ways they have seen God move in their lives as well as the lives of others.</p>
  <p class="body-copy">They believe in the manifestation of God’s power through signs and wonders.</p>
</div>
<div class="abs accordion" style="top:1041px">Our Vision<svg width="12" height="8" viewBox="0 0 12 8"><path d="M1 1l5 5 5-5" fill="none" stroke="#222" stroke-width="2"/></svg></div>
<div class="abs accordion" style="top:1095px">Our Mission<svg width="12" height="8" viewBox="0 0 12 8"><path d="M1 1l5 5 5-5" fill="none" stroke="#222" stroke-width="2"/></svg></div>

<section class="abs community"></section>
<div class="abs community-text">
  <div class="icon"></div>
  <h2 class="section-title">Join Our Community</h2>
  <p class="lead">If you are hosting an event at your church or ministry, as you prayerfully seek the Lord for guidance review these thoughts regarding Ruth Ann &amp; Daniel Hollister and their ministry.</p>
  <p class="body-copy" style="margin-top:10px">I have served in church leadership with Ruth and Daniel for several years, and I do not know of a more balanced and powerful ministry of miracles and healings. They are activators not only of supernatural demonstrations</p>
  <span class="btn">Connect With Us</span>
</div>
<div class="abs tile" style="left:646px;top:1470px;width:106px;height:168px;background:linear-gradient(160deg,#8a8f9a,#4a3a38)" role="img" aria-label="Minister speaking beside a worship leader"></div>
<div class="abs tile" style="left:762px;top:1348px;width:151px;height:183px;background:linear-gradient(160deg,#e8e6e2,#3a3538)" role="img" aria-label="Two women standing together before a cross"></div>
<div class="abs tile" style="left:922px;top:1462px;width:51px;height:69px;background:linear-gradient(160deg,#c9c3bb,#4f4744)" role="img" aria-label="Couple ministering at the front of a church"></div>
<div class="abs tile" style="left:982px;top:1470px;width:106px;height:168px;background:linear-gradient(160deg,#6f7d5c,#8e3a45 60%,#3b4a78)" role="img" aria-label="Man preaching with a microphone"></div>
<div class="abs tile" style="left:762px;top:1538px;width:51px;height:69px;background:linear-gradient(160deg,#6d8fb8,#8a4a36)" role="img" aria-label="Brick church building exterior"></div>
<div class="abs tile" style="left:822px;top:1540px;width:151px;height:182px;background:linear-gradient(180deg,#a07a46,#3a3b4e 60%,#2a2a35)" role="img" aria-label="Crowd worshipping inside a wood-ceilinged hall"></div>

<section class="abs newsletter">
  <div class="icon"></div>
  <h2>Join Our Newsletter</h2>
  <p>Signup today for free and be the first to get notified on new updates.</p>
</section>
<div class="abs field" style="left:172px;width:308px">Name</div>
<div class="abs field" style="left:503px;width:309px">Email Address</div>
<div class="abs subscribe">Subscribe</div>

<footer class="site-footer">
  <div class="brand"><span class="brand-dot" style="width:22px;height:22px"></span>Mended Held Whole</div>
  <nav class="abs footer-nav"><span>Home</span><span>About Us</span><span>Meetings &amp; Events</span><span>Lanterns by the River</span><span>Healing Rooms</span><span>Live Stream</span></nav>
  <div class="abs footer-rule"></div>
  <p class="abs copyright">Copyright © 2025 Mended Held Whole. All rights reserved.</p>
  <div class="abs social" style="left:1037px"></div>
  <div class="abs social" style="left:1067px"></div>
</footer>
</body>
</html>
```